New Bicycle shop business card

Hi!
I'm looking for a business card for my new proffesional bike mechanics shop. This shop is only for fixing broken bikes and not selling bikes.
Peferbly a modern and sleek and modern design.
Colors: black, grey, red, white
Information:
Name: Rijwielwerkplaats Vanhoutte
Shop owner: Bart Vanhoutte & Marieke Segers
Website: www.rijwielwerkplaats-vanhoutte.be
Email: info@rijwielwerkplaats-vanhoutte.be
Phone number: +32471902368
Street adres: Kerkweg 46
9940 Bellebeke
Slogan/shop information: Herstellingen van alle merken.
Logo: see files.
Target Market(s)
People who seek a mechanic to fix or upgrade their bikes.
Contact Information for Business Card
Information:
Website: info@rijwielwerkplaats-vanhoutte.be
9940 Bellebeke
Logo: see files.

```html
<!DOCTYPE html>
<html lang="nl">
<head>
<meta charset="utf-8">
<title>Rijwielwerkplaats Vanhoutte – Visitekaartje</title>
<link rel="stylesheet" href="https://fonts.googleapis.com/css2?family=Open+Sans:wght@400;600;700;800&display=swap">
<style>
  :root {
    --backdrop: #2b2b2b;
    --card-white: #ffffff;
    --card-black: #050505;
    --brand-red: #e42129;
    --ink: #1a1a1a;
    --grey: #8a8a8a;
  }
  * { box-sizing: border-box; margin: 0; padding: 0; }
  html, body { width: 1200px; height: 900px; overflow: hidden; }
  body {
    background: var(--backdrop);
    font-family: "Open Sans", Arial, sans-serif;
    position: relative;
  }
  .card {
    position: absolute;
    left: 320px;
    width: 560px;
    height: 320px;
    overflow: hidden;
    box-shadow: 0 12px 30px rgba(0,0,0,.45);
  }

  /* Back side */
  .card--back { top: 70px; background: var(--card-black); color: #fff; }
  .card--back .wordmark {
    position: absolute; left: 0; right: 0; top: 92px;
    display: flex; flex-direction: column; align-items: center;
  }
  .wordmark__dot { width: 34px; height: 34px; background: var(--brand-red); margin-bottom: 14px; }
  .wordmark__name {
    font-weight: 800; font-size: 22px; letter-spacing: 1px;
    text-transform: uppercase; line-height: 1.15; text-align: center;
  }
  .wordmark__name span { display: block; letter-spacing: 8px; }
  .card--back .slogan {
    position: absolute; left: 0; right: 0; top: 238px;
    text-align: center; font-size: 12px; font-weight: 600;
  }

  /* Front side */
  .card--front { top: 430px; background: var(--card-white); color: var(--ink); }
  .card--front .wordmark {
    position: absolute; left: 0; width: 290px; top: 86px;
    display: flex; flex-direction: column; align-items: center;
  }
  .card--front .wordmark__name { font-size: 19px; color: var(--ink); }
  .divider {
    position: absolute; left: 292px; top: 52px; width: 1.5px; height: 160px;
    background: var(--brand-red);
  }
  .details { position: absolute; left: 312px; top: 50px; width: 240px; }
  .details__label { color: var(--brand-red); font-size: 12px; font-weight: 600; }
  .details__owners { color: var(--grey); font-size: 13.5px; font-weight: 700; line-height: 1.25; margin-bottom: 6px; }
  .details__shop { color: var(--brand-red); font-size: 13.5px; font-weight: 700; }
  .details__role { font-size: 11px; font-weight: 600; margin-bottom: 8px; }
  .contact { list-style: none; }
  .contact li {
    display: flex; align-items: center; gap: 7px;
    color: var(--grey); font-size: 10.5px; line-height: 1.7;
  }
  .contact svg { width: 10px; height: 10px; flex: none; fill: var(--brand-red); }
  .address-band {
    position: absolute; left: 0; right: 0; top: 250px; height: 36px;
    background: var(--brand-red); color: #fff;
    display: flex; align-items: center; justify-content: center;
    font-size: 13px; font-weight: 600; letter-spacing: .3px;
  }
</style>
</head>
<body>

  <section class="card card--back" aria-label="Achterzijde visitekaartje">
    <div class="wordmark">
      <div class="wordmark__dot"></div>
      <div class="wordmark__name">Rijwielwerkplaats<span>Vanhoutte</span></div>
    </div>
    <p class="slogan">Herstellingen van alle merken.</p>
  </section>

  <section class="card card--front" aria-label="Voorzijde visitekaartje">
    <div class="wordmark">
      <div class="wordmark__dot"></div>
      <div class="wordmark__name">Rijwielwerkplaats<span>Vanhoutte</span></div>
    </div>

    <div class="divider"></div>

    <div class="details">
      <p class="details__label">Shop owner:</p>
      <p class="details__owners">Bart Vanhoutte &amp; Marieke Segers</p>
      <p class="details__shop">Rijwielwerkplaats Vanhoutte</p>
      <p class="details__role">General Manager</p>
      <ul class="contact">
        <li>
          <svg viewBox="0 0 24 24" aria-hidden="true"><path d="M6.6 10.8a15.2 15.2 0 0 0 6.6 6.6l2.2-2.2a1 1 0 0 1 1-.25 11.4 11.4 0 0 0 3.6.6 1 1 0 0 1 1 1V20a1 1 0 0 1-1 1A17 17 0 0 1 3 4a1 1 0 0 1 1-1h3.5a1 1 0 0 1 1 1c0 1.25.2 2.45.6 3.6a1 1 0 0 1-.25 1z"/></svg>
          +32471902368
        </li>
        <li>
          <svg viewBox="0 0 24 24" aria-hidden="true"><path d="M2 5h20v14H2z M4 7v.5l8 5 8-5V7l-8 5z" fill-rule="evenodd"/></svg>
          info@rijwielwerkplaats-vanhoutte.be
        </li>
        <li>
          <svg viewBox="0 0 24 24" aria-hidden="true"><circle cx="12" cy="12" r="10"/></svg>
          www.rijwielwerkplaats-vanhoutte.be
        </li>
      </ul>
    </div>

    <div class="address-band">Kerkweg 46 9940 Bellebeke</div>
  </section>

</body>
</html>
```